4th Generation Family Business Needs a New Card Design!

We are a family owned 4th Generation company. We are based in the Sydney, Australia area and we are desperately in need of a more modern and classy card. We are monumental masons who design, supply & erect lasting memorials throughout cemeteries in Sydney. Our customers are normally in a period of grieving. I have attached logo files that will need to be implemented on the card. Company was established 1935. Australian Owned and Operated. Card needs to be designed to PIXO.com specification.

Target Market(s)

Our target market is based upon people that a grieving for family members that have passed away. We also deal with alot of companies that own and operate cemeteries.

Industry/Entity Type

Business

Contact Information for Business Card

Simon Harcourt, Operations Manager, 0417293086, simon@harcourtmemorials.com.au
Lewis Harcourt, Director, 0491630572, lewis@harcourtmemorials.com.au
Phone # 02 9561 3048
Website: www.harcourtmemorials.com.au
Address: Suite 17, 8 Palfrey Lane, West Carlow, Sydney NSW 2156

Font styles to use
Serif
Decorative
Script

Requirements
Must have
• Would like to see the logo nicely implemented with a modern design. Embossed lettering would be a nice additive.

```html
<!DOCTYPE html>
<html lang="en">
<head>
<meta charset="utf-8">
<title>Harcourt Memorials – Business Card</title>
<link href="https://fonts.googleapis.com/css2?family=Cinzel:wght@400;600&family=Open+Sans:wght@400;600&display=swap" rel="stylesheet">
<style>
  :root {
    --backdrop: #8a8a8a;
    --brand-yellow: #f0c02c;
    --brand-gold: #e2b327;
    --ink: #1d1d1d;
    --band: #202020;
    --paper: #ffffff;
    --muted: #555555;
  }
  * { box-sizing: border-box; margin: 0; padding: 0; }
  html, body { width: 1200px; height: 950px; overflow: hidden; }
  body {
    background: var(--backdrop);
    font-family: "Open Sans", Arial, sans-serif;
    position: relative;
  }
  .card {
    position: absolute;
    left: 220px;
    width: 760px;
    height: 434px;
    overflow: hidden;
    box-shadow: 0 10px 28px rgba(0,0,0,.35);
  }

  /* Back side */
  .card--back { top: 30px; background: var(--brand-yellow); }
  .back-brand {
    position: absolute; left: 0; right: 0; top: 150px;
    text-align: center;
    font-family: "Cinzel", Georgia, serif;
    font-weight: 600;
    font-size: 44px;
    line-height: 1.1;
    color: var(--ink);
    letter-spacing: 2px;
  }
  .back-web {
    position: absolute; left: 0; right: 0; top: 330px;
    text-align: center;
    font-size: 17px;
    color: var(--ink);
  }

  /* Front side */
  .card--front { top: 486px; background: var(--paper); }
  .front-swoosh { position: absolute; inset: 0; }
  .front-brand {
    position: absolute; left: 40px; top: 200px; width: 300px;
    text-align: center;
    font-family: "Cinzel", Georgia, serif;
    font-weight: 600;
    font-size: 40px;
    line-height: 1.1;
    color: var(--ink);
    letter-spacing: 1px;
  }
  .contact { position: absolute; left: 400px; top: 62px; }
  .contact__name {
    font-family: "Cinzel", Georgia, serif;
    font-weight: 600;
    font-size: 25px;
    color: var(--ink);
    letter-spacing: 1px;
  }
  .contact__role {
    font-family: "Cinzel", Georgia, serif;
    font-size: 15px;
    color: var(--brand-gold);
    letter-spacing: 1.5px;
    margin-bottom: 16px;
  }
  .contact__address {
    font-size: 15px;
    color: var(--muted);
    line-height: 1.45;
    margin-bottom: 14px;
  }
  .contact__line {
    display: flex; align-items: center; gap: 9px;
    font-size: 14.5px;
    color: var(--muted);
    line-height: 1.6;
  }
  .contact__line svg { width: 14px; height: 14px; fill: var(--ink); flex: none; }
  .front-web {
    position: absolute; left: 350px; top: 368px;
    font-size: 17px;
    color: var(--paper);
    transform: rotate(-8deg);
    transform-origin: left center;
  }
</style>
</head>
<body>

  <section class="card card--back" aria-label="Card back">
    <div class="back-brand">Harcourt<br>Memorials</div>
    <div class="back-web">www.harcourtmemorials.com.au</div>
  </section>

  <section class="card card--front" aria-label="Card front">
    <svg class="front-swoosh" viewBox="0 0 760 434" preserveAspectRatio="none" aria-hidden="true">
      <path d="M0 420 C 250 405, 520 360, 760 270 L760 434 L0 434 Z" fill="var(--band)"/>
      <path d="M0 412 C 250 397, 520 350, 760 258" fill="none" stroke="var(--brand-yellow)" stroke-width="6"/>
    </svg>

    <div class="front-brand">Harcourt<br>Memorials</div>

    <div class="contact">
      <div class="contact__name">Simon Harcourt</div>
      <div class="contact__role">Operations Manager</div>
      <div class="contact__address">Suite 17, 8 Palfrey Lane<br>West Carlow, Sydney NSW 2156</div>
      <div class="contact__line">
        <svg viewBox="0 0 24 24"><path d="M6.6 10.8a15.1 15.1 0 0 0 6.6 6.6l2.2-2.2c.3-.3.7-.4 1-.2 1.1.4 2.3.6 3.6.6.6 0 1 .4 1 1V20c0 .6-.4 1-1 1A17 17 0 0 1 3 4c0-.6.4-1 1-1h3.5c.6 0 1 .4 1 1 0 1.3.2 2.5.6 3.6.1.3 0 .7-.2 1z"/></svg>
        02 9561 3048
      </div>
      <div class="contact__line">
        <svg viewBox="0 0 24 24"><path d="M7 1h10a2 2 0 0 1 2 2v18a2 2 0 0 1-2 2H7a2 2 0 0 1-2-2V3a2 2 0 0 1 2-2zm0 3v14h10V4zm5 15.5a1.2 1.2 0 1 0 0 2.4 1.2 1.2 0 0 0 0-2.4z"/></svg>
        0417293086
      </div>
      <div class="contact__line">
        <svg viewBox="0 0 24 24"><path d="M2 5h20v14H2zm2 2v.5l8 5 8-5V7zm0 2.8V17h16V9.8l-8 5z"/></svg>
        simon@harcourtmemorials.com.au
      </div>
    </div>

    <div class="front-web">www.harcourtmemorials.com.au</div>
  </section>

</body>
</html>
```